Law Firm Magazine Advertisement

The Company:
Thornbury Legal Partners is the largest management side women-owned employment law firm in the United States. For over a decade, we have devoted our practice exclusively to representing business in all aspects of California employment law and related litigation. Our firm represents startups to Keystone 400s from a wide range of industries including retail, restaurants, telecommunications, manufacturing, health care, finance, oil and high tech. Please see our website for more about us. www.thornburylegalpartners.example

The Ad:
We are looking for a new design for our advertisements in a major legal magazine. The magazine itself has a modern, graphical approach much like Gusto but for the legal/ business community.

Most advertisements are full page, and there is one every few pages. Some of these ads are text heavy, and others are full page photos. It is important that our ad stand out, as many of these other ads are for companies similar to us. We are looking to attract the attention of internal corporate counsel to the benefits of our outside assistance in their employment matters. We would like to maintain a professional but forward-thinking image.

We would like concepts for a full page magazine ad in black and white. We would like the designs to be based in artistic representations of our office (see photos for reference) and graphical in approach. Please do not use photos. We are looking for bold, eye-catching contrast and simple designs.

If you have any further questions, or would like clarification, please email Marisol at rtv@thornburylegalpartners.example
Updates

From looking at all of the designs that have been sent in so far, I would like to note that while we would like for the ad to fit in with our website design, we do not want it to look exactly the same. The paneled image approach is not necessarily what we are looking for. 

It is also important that the font in our logo remain the same. 

Thank you for your efforts so far.

I am in the process of obtaining more photos of our firm to post for you to use. There should be at least a few new ones by end of today or tomorrow (PST).

I have also been informed that we are removing the word "practical" from our marketing materials. Therefore, if you choose to use our words, please do not use the word "practical" in any future drafts. [I have changed this in the original brief as well, and will not penalize any designs strictly for using it, as it is easily changed later].

Our keywords are: proven, strategic, collaborative, cost effective, trial ready

We will also be adding a few additional logos to our ad for various awards and associations we are affiliated with. I will update the brief with these as soon as I have them. 

As another creative suggestion, do not shy away from adding more information about our firm. The first paragraph of the brief contains our marketing language, so feel free to integrate it into your design. 

Again, thank you for all of your efforts so far.

This project is now guaranteed! Keep up the good work and I look forward to seeing more designs.

Thank you!

Upon review of all of the designs submitted, we did not find anything like what we were looking for, and therefore I have changed the brief, and some of the requirements. Please read it again and redesign. I apologize to any designers that may have designs in the works based on the old brief and ask that you try your hand at the new request. Below is the changed wording in the brief, but please read the "must have" and "nice to have" sections again. 

Thank you.

We would like the designs to be based in artistic representations of our office (see photos for reference) and graphical in approach. Please do not use photos. We are looking for bold, eye-catching contrast and simple designs.

Reason: Updated brief with different requirements. Please re-read it. Thank you!

Industry/Entity Type

Law Firm

Requirements
Must have
• Must be black and white.

Please include:
our logo OR Thornbury Legal Partners in Futura font.
California Employment Law for Business (our tagline)
San Francisco Los Angeles (our locations, no address please)
www.thornburylegalpartners.example (our website)
FQDPA Logo
ODRT HUB Logo
Top-tier Counsel Pick Logo
Nice to have
• Artistic representation of our office

```html
<!DOCTYPE html>
<html lang="en">
<head>
<meta charset="utf-8">
<title>Thornbury Legal Partners — California Employment Law for Business</title>
<link rel="stylesheet" href="https://fonts.googleapis.com/css2?family=Arimo:wght@700&family=Jost:wght@400;500&display=swap">
<style>
  :root {
    --ink: #1c1c1c;
    --paper: #ffffff;
    --office-light: #d9d9d9;
    --office-mid: #8e8e8e;
    --office-dark: #2e2e2e;
    --seal: rgba(60, 60, 60, 0.86);
    --seal-stitch: rgba(20, 20, 20, 0.7);
    --headline: #ececec;
    --band: rgba(255, 255, 255, 0.82);
    --badge: #bdbdbd;
  }
  * { margin: 0; padding: 0; box-sizing: border-box; }
  html, body { width: 928px; height: 1200px; overflow: hidden; background: var(--paper); }
  .ad {
    position: relative;
    width: 928px;
    height: 1200px;
    overflow: hidden;
    font-family: "Jost", sans-serif;
  }
  .office-backdrop {
    position: absolute;
    inset: 0;
    background:
      linear-gradient(90deg, rgba(0,0,0,0.35) 0%, rgba(0,0,0,0) 18%, rgba(255,255,255,0.15) 40%, rgba(0,0,0,0) 60%, rgba(0,0,0,0.3) 100%),
      linear-gradient(180deg, var(--office-light) 0%, #b5b5b5 35%, var(--office-mid) 62%, var(--office-dark) 100%);
  }
  .tagline-band {
    position: absolute;
    left: 0; right: 0;
    top: 66px;
    height: 76px;
    background: var(--band);
    display: flex;
    align-items: center;
    justify-content: center;
  }
  .tagline {
    font-family: "Jost", sans-serif;
    font-weight: 400;
    font-size: 16px;
    letter-spacing: 0.26em;
    color: var(--ink);
  }
  .seal {
    position: absolute;
    left: 49px;
    top: 150px;
    width: 828px;
    height: 828px;
  }
  .values {
    position: absolute;
    left: 176px;
    top: 330px;
    transform: rotate(-10deg);
    transform-origin: 0 0;
    font-family: "Arimo", sans-serif;
    font-weight: 700;
    font-size: 86px;
    line-height: 72px;
    letter-spacing: -0.01em;
    color: var(--headline);
    list-style: none;
    white-space: nowrap;
  }
  .contact {
    position: absolute;
    left: 300px;
    top: 810px;
    transform: rotate(-13deg);
    transform-origin: 50% 50%;
    width: 480px;
    text-align: center;
    font-family: "Jost", sans-serif;
    font-size: 15px;
    line-height: 30px;
    letter-spacing: 0.3em;
    color: var(--ink);
    text-transform: uppercase;
  }
  .contact .web { letter-spacing: 0.16em; font-size: 14px; }
  .firm-name {
    position: absolute;
    left: 0; right: 0;
    top: 1104px;
    text-align: center;
    font-family: "Jost", sans-serif;
    font-weight: 500;
    font-size: 26px;
    color: var(--paper);
  }
  .badge {
    position: absolute;
    background: var(--badge);
  }
  .badge-award {
    left: 63px; top: 1075px;
    width: 86px; height: 86px;
    border-radius: 50%;
  }
  .badge-certified {
    left: 726px; top: 1092px;
    width: 120px; height: 60px;
    border-radius: 4px;
  }
</style>
</head>
<body>
  <main class="ad">
    <div class="office-backdrop" role="img" aria-label="Soft grey view of the firm's office: glass doors, window frames and a carpeted hallway"></div>

    <header class="tagline-band">
      <p class="tagline">CALIFORNIA EMPLOYMENT LAW FOR BUSINESS</p>
    </header>

    <svg class="seal" viewBox="0 0 828 828" aria-hidden="true">
      <circle cx="414" cy="414" r="414" fill="var(--seal)"/>
      <circle cx="414" cy="414" r="396" fill="none" stroke="var(--seal-stitch)" stroke-width="1.5" stroke-dasharray="9 7"/>
    </svg>

    <ul class="values">
      <li>proven</li>
      <li>strategic</li>
      <li>practical</li>
      <li>collaborative</li>
      <li>cost effective</li>
      <li>trial ready.</li>
    </ul>

    <address class="contact">
      <p class="web">www.thornburylegalpartners.example</p>
      <p>San Francisco</p>
      <p>415 555 0142</p>
    </address>

    <div class="badge badge-award" role="img" aria-label="Top-tier Counsel Pick award badge"></div>
    <p class="firm-name">Thornbury Legal Partners</p>
    <div class="badge badge-certified" role="img" aria-label="FQDPA certification badge"></div>
  </main>
</body>
</html>
```